Disability provider requiring digital flyer to promote services

My company works within the Disability sector (KTAP registered provider), currently operating in Sydney, Australia.
I require a digital brochure which lists our services and gives potential customers a quick look into what we do with a single glance.
Undecided whether this digital flyer is to be single or double sided, happy to consult with an experienced designer in this regard.
I prefer minimalist designs (which may be an issue for someone trying to convey information, I'm not sure), and possibly someone who can work with out watercolor logo.
Services include:
-Supported Independent Living
-Specialist Disability Accommodation
-Individualised Living Options Stage 1 & 2
-Home Modifications
-Occupational Therapy
-Support Coordination Levels 1 & 2
-Short Term Accommodation - STA Respite
-Drop In Supports
-Community Access
Disability

```html
<!DOCTYPE html>
<html lang="en">
<head>
<meta charset="utf-8">
<title>Clearview Care – Services</title>
<link rel="stylesheet" href="https://fonts.googleapis.com/css2?family=Jost:wght@500&family=Nunito:wght@900&family=Roboto:wght@400&display=swap">
<style>
  :root {
    --backdrop: #a4a4a4;
    --paper: #ffffff;
    --ink: #3a3a3c;
    --brand-teal: #3fbfae;
    --wash-purple: rgba(196, 130, 204, 0.75);
    --wash-violet: rgba(160, 150, 222, 0.7);
    --wash-blue: rgba(120, 170, 226, 0.7);
    --wash-sky: rgba(130, 205, 240, 0.7);
    --wash-teal: rgba(110, 200, 180, 0.65);
    --wash-green: rgba(160, 210, 90, 0.7);
    --wash-lime: rgba(215, 225, 80, 0.65);
    --icon-tile: rgba(58, 58, 60, 0.14);
  }
  * { box-sizing: border-box; margin: 0; padding: 0; }
  html, body { width: 1200px; height: 1200px; overflow: hidden; }
  body { background: var(--backdrop); position: relative; }

  .flyer {
    position: absolute;
    left: 204px; top: 40px;
    width: 792px; height: 1120px;
    background: var(--paper);
    overflow: hidden;
    color: var(--ink);
  }
  .flyer__wash {
    position: absolute; inset: 0;
    background:
      radial-gradient(ellipse 300px 260px at 95% 4%, var(--wash-purple), transparent 70%),
      radial-gradient(ellipse 380px 300px at 62% 22%, var(--wash-violet), transparent 72%),
      radial-gradient(ellipse 340px 300px at 80% 42%, var(--wash-blue), transparent 72%),
      radial-gradient(ellipse 320px 280px at 92% 62%, var(--wash-sky), transparent 72%),
      radial-gradient(ellipse 360px 260px at 70% 80%, var(--wash-teal), transparent 72%),
      radial-gradient(ellipse 420px 260px at 48% 100%, var(--wash-lime), transparent 72%),
      radial-gradient(ellipse 300px 260px at 95% 95%, var(--wash-green), transparent 72%),
      radial-gradient(ellipse 260px 240px at 10% 98%, var(--wash-green), transparent 70%);
  }

  .brand {
    position: absolute;
    left: 54px; top: 54px;
    width: 176px; height: 168px;
    display: flex; flex-direction: column; justify-content: flex-end; align-items: center;
  }
  .brand__name {
    font-family: "Jost", sans-serif;
    font-weight: 500;
    font-size: 27px;
    letter-spacing: 1px;
    color: var(--ink);
    text-transform: uppercase;
    line-height: 1;
    display: flex; align-items: center; gap: 8px;
  }
  .brand__dot {
    width: 12px; height: 12px; border-radius: 50%;
    background: var(--brand-teal);
  }

  .title {
    position: absolute;
    left: 400px; top: 104px; width: 290px;
    font-family: "Jost", sans-serif;
    font-weight: 500;
    font-size: 46px;
    line-height: 42px;
    letter-spacing: 9px;
    text-align: center;
    color: var(--ink);
  }

  .services { list-style: none; }
  .service {
    position: absolute;
    width: 220px;
    display: flex; flex-direction: column; align-items: center;
  }
  .service__icon {
    width: 68px; height: 70px;
    border-radius: 10px;
    background: var(--icon-tile);
  }
  .service__label {
    margin-top: 22px;
    font-family: "Nunito", sans-serif;
    font-weight: 900;
    font-size: 16.5px;
    line-height: 18.5px;
    letter-spacing: 1.8px;
    text-transform: uppercase;
    text-align: center;
    color: var(--ink);
  }
  .col-1 { left: 35px; }
  .col-2 { left: 287px; }
  .col-3 { left: 540px; }
  .row-1 { top: 358px; }
  .row-2 { top: 586px; }
  .row-3 { top: 802px; }

  .contact {
    position: absolute;
    left: 0; right: 0; top: 1006px;
    font-family: "Roboto", sans-serif;
    font-weight: 400;
    font-size: 18px;
    letter-spacing: 2px;
    text-align: center;
    color: var(--ink);
    line-height: 38px;
  }
</style>
</head>
<body>
  <main class="flyer">
    <div class="flyer__wash" role="img" aria-label="Soft watercolour wash in purple, blue, teal and green with paint splatters"></div>

    <div class="brand">
      <div class="brand__name"><span class="brand__dot"></span>Clearview Care</div>
    </div>

    <h1 class="title">SERVICES INCLUDE</h1>

    <ul class="services">
      <li class="service col-1 row-1"><div class="service__icon" role="img" aria-label="Line icon of a head in profile with a bird"></div><p class="service__label">Supported<br>Independent<br>Living</p></li>
      <li class="service col-2 row-1"><div class="service__icon" role="img" aria-label="Line icon of a house with a bed inside"></div><p class="service__label">Specialist<br>Disability<br>Accommodation</p></li>
      <li class="service col-3 row-1"><div class="service__icon" role="img" aria-label="Line icon of a checklist with a pointing hand"></div><p class="service__label">Individualised<br>Living Options<br>Stage 1 &amp; 2</p></li>

      <li class="service col-1 row-2"><div class="service__icon" role="img" aria-label="Line icon of a house with a window"></div><p class="service__label">Home<br>Modifications</p></li>
      <li class="service col-2 row-2"><div class="service__icon" role="img" aria-label="Line icon of a hand holding a sprouting plant"></div><p class="service__label">Occupational<br>Therapy</p></li>
      <li class="service col-3 row-2"><div class="service__icon" role="img" aria-label="Line icon of two hands raised around a group of people"></div><p class="service__label">Support<br>Coordination<br>Levels 1 &amp; 2</p></li>

      <li class="service col-1 row-3"><div class="service__icon" role="img" aria-label="Line icon of a roof over a bed"></div><p class="service__label">Short Term<br>Accommodation<br>– STA Respite</p></li>
      <li class="service col-2 row-3"><div class="service__icon" role="img" aria-label="Line icon of hands holding a group of people"></div><p class="service__label">Drop In<br>Supports</p></li>
      <li class="service col-3 row-3"><div class="service__icon" role="img" aria-label="Line icon of a door with a hand pressing a lock"></div><p class="service__label">Community<br>Access</p></li>
    </ul>

    <address class="contact" style="font-style:normal">
      +61 0400 118 362<br>
      hello@clearviewcare.com.au
    </address>
  </main>
</body>
</html>
```